Complete Website Redesign

We need a complete revamp of our website. Need to add interactive custmer catalog seection tools. Need to add customer spec input for recommended product search results. Need a cutomer lead and opportunity contact capability. Need a complete Branding message revamp. Primary visuals will be prodcut pictures and case studies.
Target Market(s)
Industrial Customers in the high durability Air movement and fan/blower space; high durability enclosure and flow industries ie. mining, chamicals, manufacturing, water treatment, chemical in use manufacturing
Look and feel
Each slider illustrates characteristics of the customer's brand and the style your logo design should communicate.

```html
<!DOCTYPE html>
<html lang="en">
<head>
<meta charset="utf-8">
<title>DFC – Durafan Composites, LLC</title>
<link href="https://fonts.googleapis.com/css2?family=Open+Sans:wght@400;600;700&family=Marcellus&display=swap" rel="stylesheet">
<style>
:root{
  --navy:#25359a;
  --navy-dark:#1f2f8f;
  --brand-red:#8d1313;
  --btn-red:#9a0f0f;
  --text:#333;
  --muted:#555;
  --panel:#2a2628;
  --panel-deep:#1c1a1b;
  --footer:#2d2a2c;
  --footer-base:#211f20;
  --orange:#e8730f;
  --sage:#7f9993;
  --line:#d8d8d8;
}
*{margin:0;padding:0;box-sizing:border-box}
html,body{width:1200px;height:1000px;overflow:hidden;background:#fff}
body{position:relative;font-family:"Open Sans",Arial,sans-serif;color:var(--text)}
.abs{position:absolute}
.top-rule{left:0;top:0;width:1200px;height:5px;background:var(--navy-dark)}
.brand{left:55px;top:18px;display:flex;flex-direction:column}
.brand-row{display:flex;align-items:center;gap:12px}
.brand-mark{width:38px;height:38px;background:var(--navy)}
.brand-name{font-size:40px;font-weight:600;color:var(--navy);line-height:1}
.brand-sub{margin-top:8px;font-size:14px;font-weight:600;color:var(--navy)}
.call{left:535px;top:14px;font-size:21px;font-weight:600;letter-spacing:.5px;color:#333}
.call span{color:var(--brand-red)}
.account{left:1028px;top:19px;font-size:12px;color:var(--navy)}
.account i{font-style:normal;margin:0 9px;color:#888}
.nav{top:66px;font-size:12px;color:#555;text-transform:uppercase;letter-spacing:.3px}
.nav.active{color:var(--navy)}
.nav-underline{left:525px;top:82px;width:52px;height:2px;background:var(--navy)}
.header-rule{left:35px;top:94px;width:1116px;height:1px;background:var(--line)}
.hero{left:40px;top:95px;width:1106px;height:285px;background:linear-gradient(#f7f7f7,#e6e6e6)}
.hero-visual{left:140px;top:115px;width:910px;height:200px;border-radius:4px;background:linear-gradient(90deg,#b9bdcc,#d4d6de 50%,#b3b7c7)}
.hero-caption{left:40px;top:322px;width:1106px;text-align:center;font-family:"Marcellus",serif;font-size:19px;line-height:25px;color:#333;letter-spacing:.4px}
.selector-shadow{left:105px;top:446px;width:970px;height:24px;background:linear-gradient(#bdbdbd,#e6e6e6);clip-path:polygon(0 0,100% 0,99% 100%,1% 100%)}
.selector{left:78px;top:380px;width:1024px;height:68px;background:var(--panel)}
.selector-label{left:163px;top:13px;font-size:18px;font-weight:600;color:#fff}
.selector-input{left:349px;top:10px;width:424px;height:27px;background:var(--panel-deep);border:1px solid #555}
.selector-btn{left:784px;top:13px;width:76px;height:22px;border-radius:4px;background:var(--sage);color:#fff;font-size:12px;font-weight:600;text-align:center;line-height:22px}
.selector-hint{left:0;top:47px;width:1024px;text-align:center;font-size:11px;font-weight:600;color:var(--orange);padding-left:150px}
.section-rule{top:491px;height:1px;background:var(--line)}
.section-title{left:0;top:478px;width:1166px;text-align:center;font-size:19px;color:var(--brand-red);letter-spacing:.5px}
.card{top:547px;width:165px;height:211px;border:1px solid #d4d4d4;background:#fff}
.card-tab{top:551px;width:189px;height:29px;background:var(--navy);color:#fff;font-size:14px;font-weight:600;text-align:center;line-height:28px;white-space:nowrap}
.card-visual{position:absolute;left:18px;top:40px;width:130px;height:140px;border-radius:3px;background:radial-gradient(circle,#c9ccd6,#e9eaee 75%)}
.card-more{position:absolute;right:-1px;bottom:-1px;width:78px;height:20px;background:var(--btn-red);clip-path:polygon(22% 0,100% 0,100% 100%,0 100%);color:#fff;font-size:12px;font-weight:600;text-align:right;padding-right:8px;line-height:20px}
.footer{left:0;top:817px;width:1200px;height:140px;background:var(--footer)}
.footer-base{left:0;top:957px;width:1200px;height:43px;background:var(--footer-base);color:#bbb;font-size:13px;text-align:center;line-height:52px}
.footer-heading{top:826px;width:200px;text-align:center;font-size:13.5px;font-weight:600;color:#fff}
.quote{left:74px;top:849px;width:196px;height:81px;border-radius:10px;background:#1a1a1a;color:#fff;font-size:10px;line-height:12.6px;padding:8px 12px 0 10px;text-align:justify}
.quote b{color:#e01f1f;font-weight:400}
.quote-tail{left:160px;top:928px}
.quote-author{left:210px;top:939px;font-size:11px;color:#fff}
.social{width:31px;height:31px;border-radius:7px}
.form-panel{top:849px;width:236px;height:108px;border-radius:8px 8px 0 0;background:var(--footer-base)}
.field{position:absolute;height:21px;background:#39363a;color:#aaa;font-size:11px;padding:2px 9px}
.btn{position:absolute;height:17px;color:#fff;font-size:11px;font-weight:600;text-align:center;line-height:17px}
.btn.red{background:var(--btn-red)}
.btn.blue{background:#3a6ea5}
</style>
</head>
<body>
<div class="abs top-rule"></div>

<div class="abs brand">
  <div class="brand-row"><div class="brand-mark"></div><div class="brand-name">DFC</div></div>
  <div class="brand-sub">Durafan Composites, LLC</div>
</div>

<div class="abs call"><span>CALL US :</span> +1 (800) 123 456 789</div>
<div class="abs account">LOGIN<i>|</i>SIGNUP</div>

<div class="abs nav active" style="left:534px">Home</div>
<div class="abs nav" style="left:610px">Products</div>
<svg class="abs" style="left:682px;top:68px" width="6" height="9" viewBox="0 0 6 9"><path d="M3 0v7M1 5l2 3 2-3" stroke="#555" fill="none"/></svg>
<div class="abs nav" style="left:712px">About Us</div>
<div class="abs nav" style="left:810px">Mission</div>
<div class="abs nav" style="left:896px">Request Information</div>
<div class="abs nav" style="left:1066px">Contacts</div>
<div class="abs nav-underline"></div>
<div class="abs header-rule"></div>

<div class="abs hero"></div>
<div class="abs hero-visual" role="img" aria-label="Photos of fiberglass axial fan, centrifugal blower, high plume exhaust fans and roof ventilator"></div>
<div class="abs hero-caption">WE HAVE A WIDE SELECION OF FIBERGLASS FANS AND OTHER CORROSION RESISTANT AIR HANDLING<br>SOLUTIONS FOR OEMS, CONTRACTORS AND PLANT MAINTENANCE OPERATIONS.</div>

<div class="abs selector-shadow"></div>
<div class="abs selector">
  <div class="abs selector-label">PRODUCT SELECTION</div>
  <div class="abs selector-input"></div>
  <div class="abs selector-btn">Submit</div>
  <div class="abs selector-hint">To verify a catalog number and access product information, enter the complete number (including dashes) above.</div>
</div>

<div class="abs section-rule" style="left:55px;width:445px"></div>
<div class="abs section-rule" style="left:665px;width:455px"></div>
<div class="abs section-title">OUR PRODUCTS</div>

<div class="abs card" style="left:60px"><div class="card-visual" role="img" aria-label="Fiberglass centrifugal fan photo"></div><div class="card-more">more &gt;&gt;</div></div>
<div class="abs card-tab" style="left:49px">Fiberglass Centrifugal Fans</div>
<div class="abs card" style="left:287px"><div class="card-visual" role="img" aria-label="High plume exhaust fans photo"></div><div class="card-more">more &gt;&gt;</div></div>
<div class="abs card-tab" style="left:276px">High Plume Exhaust Fans</div>
<div class="abs card" style="left:520px"><div class="card-visual" role="img" aria-label="Fiberglass damper photo"></div><div class="card-more">more &gt;&gt;</div></div>
<div class="abs card-tab" style="left:509px;font-size:13px">Fiberglass Louvers &amp; Dampers</div>
<div class="abs card" style="left:747px"><div class="card-visual" role="img" aria-label="Fiberglass axial propeller photo"></div><div class="card-more">more &gt;&gt;</div></div>
<div class="abs card-tab" style="left:736px">Fiberglass axial Propellers</div>
<div class="abs card" style="left:973px"><div class="card-visual" role="img" aria-label="Fiberglass axial fan photo"></div><div class="card-more">more &gt;&gt;</div></div>
<div class="abs card-tab" style="left:962px">Fiberglass Axial Fans</div>

<div class="abs footer"></div>
<div class="abs footer-heading" style="left:64px">TESTIMONIALS</div>
<div class="abs footer-heading" style="left:314px">FOLLOW US</div>
<div class="abs footer-heading" style="left:577px">NEWSLETTER</div>
<div class="abs footer-heading" style="left:870px">QUICK CONACT</div>

<div class="abs quote">I have been very satisfied with all of the service provided by <b>DFC</b>. All of your personnel are really focused and were so courteous and professional acting.</div>
<svg class="abs quote-tail" width="40" height="24" viewBox="0 0 40 24"><path d="M0 0h36L30 22Z" fill="#1a1a1a"/></svg>
<div class="abs quote-author">Mr. Abc</div>

<div class="abs social" style="left:342px;top:855px;background:#2aa3d8" aria-label="Social link"></div>
<div class="abs social" style="left:380px;top:855px;background:#c9231d" aria-label="Social link"></div>
<div class="abs social" style="left:417px;top:855px;background:#3b5a9a" aria-label="Social link"></div>
<div class="abs social" style="left:454px;top:855px;background:#1a6fa8" aria-label="Social link"></div>
<div class="abs social" style="left:342px;top:897px;background:#b8161c" aria-label="Social link"></div>
<div class="abs social" style="left:381px;top:897px;background:#3aa33a" aria-label="Share"></div>
<div class="abs social" style="left:418px;top:897px;background:#f07a1a" aria-label="Feed"></div>

<div class="abs form-panel" style="left:564px">
  <div class="field" style="left:23px;top:12px;width:194px">Your Name</div>
  <div class="field" style="left:23px;top:40px;width:194px">Your Email</div>
  <div class="btn red" style="left:163px;top:85px;width:52px">Submit</div>
</div>
<div class="abs form-panel" style="left:858px">
  <div class="field" style="left:18px;top:12px;width:194px">Your Email</div>
  <div class="field" style="left:18px;top:40px;width:194px;height:39px">Your Message</div>
  <div class="btn blue" style="left:99px;top:85px;width:52px">Reset</div>
  <div class="btn red" style="left:160px;top:85px;width:51px">Submit</div>
</div>

<div class="abs footer-base">Copyright ©&nbsp; DFC&nbsp; 2013. All rights reserved.</div>
</body>
</html>
```